Business Card For Halvenmoor Financial Consulting

Hi, I would like a business card designed. Bold, modern.
Please use the same design as the logo. I have also attached the website design to see the overall theme.
Wordmark Font
Color: Hex: #01AEF7

```html
<!DOCTYPE html>
<html lang="en">
<head>
<meta charset="utf-8">
<title>Halvenmoor Financial Consulting – Business Card</title>
<link rel="stylesheet" href="https://fonts.googleapis.com/css2?family=Open+Sans:wght@400;600;700&display=swap">
<style>
  :root {
    --backdrop: #232323;
    --card-navy: #0a4469;
    --accent-blue: #2ba6df;
    --text-white: #ffffff;
    --divider: rgba(255,255,255,0.75);
  }
  * { margin: 0; padding: 0; box-sizing: border-box; }
  html, body {
    width: 1200px; height: 780px; overflow: hidden;
    background: var(--backdrop);
    font-family: "Open Sans", Arial, sans-serif;
  }
  .stage {
    position: relative; width: 1200px; height: 780px;
    display: flex; align-items: center; justify-content: center; gap: 40px;
  }
  .card {
    position: relative; width: 540px; height: 309px;
    background: var(--card-navy);
    box-shadow: 0 10px 24px rgba(0,0,0,0.55);
    overflow: hidden;
  }
  /* Front */
  .card-front { display: flex; align-items: center; justify-content: center; gap: 18px; }
  .brand-square {
    width: 54px; height: 54px;
    border: 5px solid var(--accent-blue);
    flex: none;
  }
  .brand-name {
    color: var(--text-white);
    font-weight: 700;
    font-size: 25px;
    line-height: 1.2;
    letter-spacing: 1.5px;
    text-transform: uppercase;
  }
  /* Back */
  .card-back { display: flex; align-items: center; }
  .person {
    width: 240px; padding-left: 38px; padding-top: 70px;
  }
  .person-name {
    color: var(--accent-blue); font-weight: 700; font-size: 25px; line-height: 1.1;
  }
  .person-title {
    color: var(--text-white); font-weight: 400; font-size: 14px; margin-top: 4px;
  }
  .divider {
    width: 1px; height: 150px; background: var(--divider);
    margin: 0 28px 0 6px;
  }
  .contact { color: var(--text-white); font-size: 13px; line-height: 1.5; }
  .contact-address { margin-bottom: 10px; }
  .contact-row { display: flex; align-items: center; gap: 8px; }
  .contact-icon { width: 13px; height: 13px; flex: none; }
</style>
</head>
<body>
<main class="stage">
  <section class="card card-front" aria-label="Card front">
    <span class="brand-square" aria-hidden="true"></span>
    <div class="brand-name">Halvenmoor<br>Financial Consulting</div>
  </section>

  <section class="card card-back" aria-label="Card back">
    <div class="person">
      <p class="person-name">Marta Kovalenko</p>
      <p class="person-title">Managing Director</p>
    </div>
    <span class="divider" aria-hidden="true"></span>
    <div class="contact">
      <p class="contact-address">1840 Larkfield Ave. Suite 310<br>Brookhaven, TX 75390</p>
      <p class="contact-row">
        <svg class="contact-icon" viewBox="0 0 24 24" aria-hidden="true"><path fill="#2ba6df" d="M6.6 10.8a15.1 15.1 0 0 0 6.6 6.6l2.2-2.2c.3-.3.7-.4 1-.2 1.1.4 2.3.6 3.6.6.6 0 1 .4 1 1V20c0 .6-.4 1-1 1A17 17 0 0 1 3 4c0-.6.4-1 1-1h3.5c.6 0 1 .4 1 1 0 1.3.2 2.5.6 3.6.1.3 0 .7-.2 1z"/></svg>
        (555) 214-6083
      </p>
      <p class="contact-row">
        <svg class="contact-icon" viewBox="0 0 24 24" aria-hidden="true"><rect x="2" y="5" width="20" height="14" rx="1.5" fill="#2ba6df"/><path d="M3 6l9 7 9-7" fill="none" stroke="#0a4469" stroke-width="1.8"/></svg>
        info@website.com
      </p>
      <p class="contact-row">
        <svg class="contact-icon" viewBox="0 0 24 24" aria-hidden="true"><circle cx="12" cy="12" r="10" fill="#2ba6df"/><path d="M2 12h20M12 2c3 3 3 17 0 20M12 2c-3 3-3 17 0 20" fill="none" stroke="#0a4469" stroke-width="1.5"/></svg>
        www.website.com
      </p>
    </div>
  </section>
</main>
</body>
</html>
```